web page design with coding

We are a start up insurance agency who needs to design a full functional web page. we recently did a postcard design though drawkettle I will upload the final project for you to see the color scheme/font we would like to continue to use. I also have a rough draft of verbage I would like our website to have. I will upload that as well.

Reason: I am sorry but the person who will make the final decision on the website is out of the country at the moment and will make the final decision when he returns.

Industry/Entity Type

Insurance

Coding

Coded - Design and coding required

```html
<!DOCTYPE html>
<html lang="en">
<head>
<meta charset="utf-8">
<title>Meridale Insurance Group</title>
<link href="https://fonts.googleapis.com/css2?family=Lora:ital,wght@0,400;0,600;1,400&family=Open+Sans:wght@400;600;700&display=swap" rel="stylesheet">
<style>
:root{
  --navy:#1d2740;
  --navy-deep:#161e33;
  --orange:#f28a12;
  --ink:#333a46;
  --muted:#8a8f98;
  --rule:#e3e3e3;
  --paper:#ffffff;
  --mist:#f3f3f3;
  --serif:'Lora', Georgia, serif;
  --sans:'Open Sans', Arial, sans-serif;
}
*{box-sizing:border-box;margin:0;padding:0}
html,body{width:1200px;height:2836px;overflow:hidden;background:var(--paper)}
body{font-family:var(--serif);color:var(--ink);position:relative}

/* header + hero */
.hero{position:absolute;left:0;top:0;width:1200px;height:628px}
.hero-photo{position:absolute;inset:0;background:
  linear-gradient(180deg,#b9c6d3 0%,#d6dde4 30%,#a08670 48%,#8c705a 62%,#6f8a3e 78%,#59762f 100%)}
.topbar{position:absolute;left:0;top:0;width:1200px;height:80px;background:rgba(29,39,64,.92)}
.brand{position:absolute;left:80px;top:0;height:80px;display:flex;align-items:center;gap:12px;
  font-family:var(--sans);font-weight:700;font-size:18px;color:#fff;white-space:nowrap}
.brand .square{width:20px;height:20px;background:var(--orange)}
.nav{position:absolute;right:80px;top:0;height:80px;display:flex;align-items:center;gap:40px;
  font-family:var(--sans);font-size:14px;font-weight:600;color:#fff;letter-spacing:.5px}
.nav .quote{background:var(--orange);padding:12px 18px;border-radius:2px}
.hero-box{position:absolute;left:60px;top:262px;width:420px;height:218px;background:rgba(255,255,255,.82);padding:26px 28px}
.hero-box h1{font-family:var(--serif);font-style:italic;font-weight:600;font-size:28px;color:var(--navy)}
.hero-box p{font-style:italic;font-size:13px;line-height:1.7;color:#555;margin-top:12px}
.hero-box .more{display:block;margin-top:14px;font-size:14px;font-weight:600;color:var(--navy)}
.dots{position:absolute;left:550px;top:592px;display:flex;gap:10px}
.dots span{width:16px;height:16px;border:2px solid #fff;border-radius:50%}
.dots span.on{background:#fff}

/* section headings */
.section-title{text-align:center;font-family:var(--sans);font-weight:600;font-size:26px;letter-spacing:1px}
.section-title b{font-weight:700}
.section-lead{text-align:center;font-style:italic;font-size:14px;line-height:1.7;color:var(--muted);width:720px;margin:14px auto 0}

/* welcome */
.welcome{position:absolute;left:0;top:628px;width:1200px;height:540px;background:var(--paper);padding-top:40px}
.welcome .section-title{color:var(--ink)}
.service-card{position:absolute;top:152px;width:380px;height:320px;background:var(--paper);
  box-shadow:0 2px 10px rgba(0,0,0,.12);text-align:center;padding-top:30px}
.service-card.business{left:228px}
.service-card.personal{left:628px}
.service-card h2{font-family:var(--serif);font-style:italic;font-weight:600;font-size:22px;margin-top:14px;color:var(--ink)}
.service-card p{font-style:italic;font-size:13px;line-height:1.7;color:var(--muted);width:290px;margin:12px auto 0}
.btn{display:inline-block;margin-top:22px;padding:9px 22px;font-family:var(--sans);font-size:13px;color:#fff;border-radius:2px}
.btn.orange{background:var(--orange)}
.btn.dark{background:var(--navy)}

/* blog */
.blog{position:absolute;left:0;top:1168px;width:1200px;height:572px;background:var(--mist);padding-top:30px;border-top:1px solid var(--rule)}
.post{position:absolute;top:150px;width:304px}
.post.p1{left:88px}.post.p2{left:448px}.post.p3{left:792px}
.post-photo{width:304px;height:212px}
.post h3{font-family:var(--serif);font-weight:400;font-size:22px;margin-top:24px;color:var(--ink)}
.post .meta{font-family:var(--sans);font-size:10px;color:var(--muted);margin-top:10px;display:flex;gap:16px}
.post p{font-size:12px;line-height:1.7;color:#666;margin-top:10px}

/* agents */
.agents{position:absolute;left:0;top:1740px;width:1200px;height:372px;background:var(--navy);padding-top:34px;color:#fff}
.agents .section-title{color:#fff}
.agents .section-lead{color:#c5cad6;margin-top:10px}
.agent-card{position:absolute;top:160px;width:500px;height:180px;background:var(--paper);display:flex;align-items:center;padding:0 24px}
.agent-card.a1{left:80px}.agent-card.a2{left:620px}
.agent-photo{flex:0 0 116px;height:116px;border-radius:50%}
.agent-body{margin-left:24px;color:var(--ink)}
.agent-body p{font-style:italic;font-size:12px;line-height:1.7;color:#666}
.agent-foot{display:flex;justify-content:space-between;align-items:center;margin-top:14px}
.agent-name{font-family:var(--sans);font-size:11px;color:var(--orange);font-weight:700}
.agent-role{font-family:var(--sans);font-size:10px;color:var(--muted)}
.agent-btn{border:1px solid var(--rule);font-family:var(--sans);font-size:11px;padding:7px 14px;color:var(--ink)}

/* about */
.about{position:absolute;left:0;top:2112px;width:1200px;height:416px;background:linear-gradient(180deg,#f1f1f1,#e8e8e8)}
.about h2{position:absolute;left:88px;top:44px;font-family:var(--sans);font-size:26px;font-weight:400;color:var(--ink)}
.about h2 b{font-weight:700}
.about-text{position:absolute;left:88px;top:104px;width:520px}
.about-text p{font-style:italic;font-size:13px;line-height:1.8;color:#777;margin-bottom:16px}
.about-art{position:absolute;left:700px;top:40px;width:400px;height:360px}

/* footer */
.footer{position:absolute;left:0;top:2528px;width:1200px;height:232px;background:var(--paper);border-top:1px solid var(--rule)}
.footer-brand{position:absolute;left:88px;top:30px;display:flex;align-items:center;gap:12px;
  font-family:var(--sans);font-weight:700;font-size:17px;color:var(--navy);white-space:nowrap}
.footer-brand .square{width:22px;height:22px;background:var(--navy)}
.col{position:absolute;top:30px}
.col h4{font-family:var(--sans);font-size:15px;font-weight:700;color:var(--ink);margin-bottom:16px}
.col.contact{left:368px;width:230px}
.col.news{left:632px;width:240px}
.col.follow{left:888px;width:240px}
.contact-row{display:flex;align-items:flex-start;gap:10px;font-family:var(--sans);font-size:11px;color:#666;margin-bottom:12px;line-height:1.5}
.contact-row svg{flex:0 0 14px;margin-top:2px}
.col p{font-family:var(--sans);font-size:11px;line-height:1.6;color:#666}
.field{margin-top:14px;width:220px;height:30px;border:1px solid var(--rule);font-family:var(--sans);font-size:11px;color:#aaa;padding:7px 10px}
.subscribe{display:inline-block;margin-top:10px;background:var(--navy);color:#fff;font-family:var(--sans);font-size:11px;padding:7px 14px}
.social{display:flex;gap:10px;margin-top:16px}
.social span{width:30px;height:30px;border:1px solid #bbb;border-radius:50%}
.bottombar{position:absolute;left:0;top:2760px;width:1200px;height:76px;background:var(--navy-deep);
  display:flex;align-items:center;justify-content:center;font-family:var(--sans);font-size:12px;color:#aab}
</style>
</head>
<body>

<header class="hero">
  <div class="hero-photo" role="img" aria-label="Photograph of a two-storey family house with a lawn and trees under a pale sky"></div>
  <div class="topbar"></div>
  <div class="brand"><span class="square"></span><span>Meridale Insurance Group</span></div>
  <nav class="nav">
    <span>HOME</span><span>ABOUT US</span><span>SERVICES</span><span>PROJECTS</span><span>NEWS</span><span>CONTACT</span>
    <span class="quote">GET A QUOTE</span>
  </nav>
  <div class="hero-box">
    <h1>Meridale Insurance Group</h1>
    <p>Meridale Insurance Group has joined with regional and national insurance companies to provide quality peace of mind for every decision you make.</p>
    <span class="more">Read More</span>
  </div>
  <div class="dots"><span class="on"></span><span></span><span></span></div>
</header>

<section class="welcome">
  <h2 class="section-title">WELCOME TO <b>MIG</b></h2>
  <p class="section-lead">Meridale Insurance Group has joined with regional and national insurance companies to provide quality peace of mind so the decision making process becomes an informed encounter.</p>

  <article class="service-card business">
    <svg width="52" height="52" viewBox="0 0 52 52"><rect x="8" y="18" width="36" height="26" rx="3" fill="#333a46"/><rect x="19" y="10" width="14" height="9" rx="2" fill="none" stroke="#333a46" stroke-width="3"/><rect x="8" y="28" width="36" height="3" fill="#fff"/></svg>
    <h2>Business Insurance</h2>
    <p>Meridale Insurance Group has joined with regional and national insurance companies to provide quality protection for your business and team.</p>
    <span class="btn orange">View More</span>
  </article>

  <article class="service-card personal">
    <svg width="52" height="52" viewBox="0 0 52 52"><path d="M6 26 L26 8 L46 26" fill="none" stroke="#333a46" stroke-width="4"/><rect x="12" y="24" width="28" height="20" fill="#333a46"/><rect x="22" y="32" width="8" height="12" fill="#fff"/></svg>
    <h2>Personal Insurance</h2>
    <p>Meridale Insurance Group has joined with regional and national insurance companies to provide quality cover for your home and family.</p>
    <span class="btn dark">View More</span>
  </article>
</section>

<section class="blog">
  <h2 class="section-title">LATEST <b>BLOG</b></h2>
  <p class="section-lead">Meridale Insurance Group has joined with regional and national insurance companies to provide quality peace of mind so the decision making process becomes an informed encounter.</p>

  <article class="post p1">
    <div class="post-photo" role="img" aria-label="Photograph of hands signing an insurance form with a pen" style="background:linear-gradient(135deg,#dfe6ec,#9fb2c2 60%,#6f879c)"></div>
    <h3>Contrary to Popular</h3>
    <div class="meta"><span>12 March 2016</span><span>By Admin</span><span>3 Likes</span></div>
    <p>Neque porro quisquam est, qui dolorem ipsum quia sit amet, consectetur, adipisci velit, sed quia non numquam eius modi tempora incidunt.</p>
  </article>
  <article class="post p2">
    <div class="post-photo" role="img" aria-label="Photograph of two hands sheltering a small toy car" style="background:linear-gradient(135deg,#eef1f4,#c9d3dc 50%,#4f6a8f)"></div>
    <h3>Contrary to Popular</h3>
    <div class="meta"><span>12 March 2016</span><span>By Admin</span><span>3 Likes</span></div>
    <p>Neque porro quisquam est, qui dolorem ipsum quia sit amet, consectetur, adipisci velit, sed quia non numquam eius modi tempora incidunt.</p>
  </article>
  <article class="post p3">
    <div class="post-photo" role="img" aria-label="Photograph of an agent meeting a couple at a desk" style="background:linear-gradient(135deg,#d8cfc4,#8f7c6b 50%,#2f333b)"></div>
    <h3>Contrary to Popular</h3>
    <div class="meta"><span>12 March 2016</span><span>By Admin</span><span>3 Likes</span></div>
    <p>Neque porro quisquam est, qui dolorem ipsum quia sit amet, consectetur, adipisci velit, sed quia non numquam eius modi tempora incidunt.</p>
  </article>
</section>

<section class="agents">
  <h2 class="section-title">OUR <b>AGENTS</b></h2>
  <p class="section-lead">Meridale Insurance Group has joined with regional and national insurance companies to provide quality peace of mind so the decision making process becomes an informed encounter.</p>

  <article class="agent-card a1">
    <div class="agent-photo" role="img" aria-label="Portrait photograph of a female agent" style="background:radial-gradient(circle at 50% 40%,#d9c4b4,#6b5446)"></div>
    <div class="agent-body">
      <p>Before years of experience protecting Meridale clients, she worked across independent agencies and now helps families find cover that fits their needs.</p>
      <div class="agent-foot">
        <div><div class="agent-name">JANE MORROW</div><div class="agent-role">Owner and Producer</div></div>
        <span class="agent-btn">Read More</span>
      </div>
    </div>
  </article>
  <article class="agent-card a2">
    <div class="agent-photo" role="img" aria-label="Portrait photograph of a male agent" style="background:radial-gradient(circle at 50% 40%,#d4c0ae,#4a4a52)"></div>
    <div class="agent-body">
      <p>Before years of experience protecting Meridale clients, he worked across independent agencies and now helps businesses find cover that fits their needs.</p>
      <div class="agent-foot">
        <div><div class="agent-name">OWEN LASKER</div><div class="agent-role">Owner and Producer</div></div>
        <span class="agent-btn">Read More</span>
      </div>
    </div>
  </article>
</section>

<section class="about">
  <h2>ABOUT <b>US</b></h2>
  <div class="about-text">
    <p>Meridale Insurance Group has joined with regional and national insurance companies to provide quality products and superior service. We take the time to learn your needs and coverage, not to just sell insurance products. We strive to ensure you are informed before every decision.</p>
    <p>We specialize in commercial business and personal insurance. We are committed to providing personal attention to all your insurance needs. At Meridale Insurance Group we are independent insurance agents. As independent agents, we do not work for any one company.</p>
  </div>
  <div class="about-art" role="img" aria-label="Illustration of a small house on a patch of grass resting in an open hand" style="background:radial-gradient(ellipse at 50% 45%,#9fb5c6 0%,#b8c9a3 35%,#e6c9ab 60%,rgba(232,232,232,0) 72%)"></div>
</section>

<footer class="footer">
  <div class="footer-brand"><span class="square"></span><span>Meridale Insurance Group</span></div>

  <div class="col contact">
    <h4>CONTACT US</h4>
    <div class="contact-row"><svg width="14" height="14" viewBox="0 0 14 14"><path d="M3 1 L5 1 L6 4 L4.5 5.5 Q6 8.5 8.5 9.5 L10 8 L13 9 L13 11 Q13 13 11 13 Q2 12 1 3 Q1 1 3 1Z" fill="#777"/></svg><span>(555) 014-2800 (Phone)</span></div>
    <div class="contact-row"><svg width="14" height="14" viewBox="0 0 14 14"><rect x="1" y="3" width="12" height="8" fill="none" stroke="#777" stroke-width="1.4"/><path d="M1 3 L7 8 L13 3" fill="none" stroke="#777" stroke-width="1.4"/></svg><span>hello@meridale.example</span></div>
    <div class="contact-row"><svg width="14" height="14" viewBox="0 0 14 14"><path d="M7 13 Q2 7 2 5 A5 5 0 0 1 12 5 Q12 7 7 13Z" fill="#777"/><circle cx="7" cy="5" r="1.8" fill="#fff"/></svg><span>1482 Fernwood Road Suite 210<br>Harlow, CA 90210</span></div>
  </div>

  <div class="col news">
    <h4>NEWSLETTER</h4>
    <p>Register your email address to get information about us.</p>
    <div class="field">Email Address</div>
    <span class="subscribe">Subscribe</span>
  </div>

  <div class="col follow">
    <h4>FOLLOW US</h4>
    <p>Stay in touch with our agents for tips, news and updates on coverage.</p>
    <div class="social"><span></span><span></span><span></span><span></span><span></span></div>
  </div>
</footer>

<div class="bottombar">© Copyright 2016 MIG. All Rights Reserved</div>

</body>
</html>
```